Company identity deisgn should support 2 languages

I would like to get our company identity design
This includes the following only
Business Cards 2 languages Arabic and English
Email signature
Letterhead
Linkedin profile images
Attached is the logo in Ai format

Requirements
Must have
• For business card
Must have
Name and Adrees in arabic
Name and Address in english
You might use both side of the card
Should not have
• Any pictures other than the logo

```html
<!DOCTYPE html>
<html lang="en">
<head>
<meta charset="utf-8">
<title>Northfield Logic Systems – Letterhead</title>
<link rel="stylesheet" href="https://fonts.googleapis.com/css2?family=Open+Sans:wght@400;600&family=Roboto:wght@400&display=swap">
<style>
  :root {
    --backdrop: #e4e4e4;
    --paper: #fafafa;
    --brand-blue: #1474bb;
    --brand-grey: #6a6b6f;
    --text-dark: #4a4a4a;
    --text-body: #555555;
    --signature-tone: #e9e9e9;
  }
  * { margin: 0; padding: 0; box-sizing: border-box; }
  html, body {
    width: 1200px; height: 800px; overflow: hidden;
    background: var(--backdrop);
  }
  .letterhead {
    position: absolute; left: 327px; top: 20px;
    width: 545px; height: 760px;
    background: var(--paper);
    font-family: "Open Sans", sans-serif;
    color: var(--text-body);
  }
  .brand {
    position: absolute; left: 49px; top: 88px;
    display: flex; align-items: center; gap: 7px;
  }
  .brand-dot {
    width: 14px; height: 14px; border-radius: 50%;
    background: var(--brand-blue);
  }
  .brand-name {
    font-size: 11px; font-weight: 600; letter-spacing: 0.02em;
    color: var(--brand-blue); text-transform: uppercase;
  }
  .contact {
    position: absolute; left: 350px; top: 56px;
    font-family: "Roboto", sans-serif;
    font-size: 12.3px; line-height: 15.5px;
    color: var(--text-dark);
    list-style: none;
  }
  .contact .address { margin-bottom: 3px; }
  .contact li { display: flex; align-items: center; gap: 4px; }
  .contact svg { width: 11px; height: 11px; flex: none; }
  .letter-body {
    position: absolute; left: 49px; top: 197px; width: 447px;
    font-size: 9.9px; line-height: 14.7px;
  }
  .letter-body p { text-align: justify; margin-bottom: 14.7px; }
  .letter-body .salutation { margin-bottom: 14.7px; }
  .letter-body .closing { margin-top: 29px; }
  .signature {
    position: absolute; left: 49px; top: 540px;
    width: 64px; height: 62px;
    background: var(--signature-tone);
  }
  .footer-band {
    position: absolute; left: 0; bottom: 0;
    width: 545px; height: 11px; display: block;
  }
</style>
</head>
<body>
  <main class="letterhead">
    <div class="brand">
      <span class="brand-dot"></span>
      <span class="brand-name">Northfield Logic Systems</span>
    </div>

    <ul class="contact">
      <li class="address">42 Cedar Ridge Rd, Vernon<br>B.C. Canada V1T 2K9</li>
      <li>
        <svg viewBox="0 0 12 12" aria-hidden="true"><path fill="#1474bb" d="M1 4c0-2 10-2 10 0v1H8V4H4v1H1zM3 6h6l2 4H1z"/></svg>
        555.204.7781
      </li>
      <li>
        <svg viewBox="0 0 12 12" aria-hidden="true"><rect x="1" y="2.5" width="10" height="7" fill="#1474bb"/><path d="M1 2.5l5 4 5-4M1 9.5l3.5-3.5M11 9.5L7.5 6" stroke="#fff" stroke-width=".9" fill="none"/></svg>
        info@northfieldmail.com
      </li>
      <li>
        <svg viewBox="0 0 12 12" aria-hidden="true"><circle cx="6" cy="6" r="5" fill="#1474bb"/><path d="M3 3.5c1.5 0 2 1 1.5 2S6 7 5.5 9M8 2.5c-.5 1.5.5 2 1.5 2.5" stroke="#fff" stroke-width=".9" fill="none"/></svg>
        www.northfieldweb.com
      </li>
    </ul>

    <section class="letter-body">
      <p class="salutation">Dear customer,</p>
      <p>Lorem ipsum dolor sit amet, consectetur adipisicing elit, sed do eiusmod tempor incididunt ut labore et dolore magna aliqua. Ut enim ad minim veniam, quis nostrud exercitation ullamco laboris nisi ut aliquip ex ea commodo consequat. Duis aute irure dolor in reprehenderit in voluptate velit esse cillum dolore eu fugiat nulla pariatur. Excepteur sint occaecat cupidatat non proident, sunt in culpa qui officia deserunt mollit anim id est laborum.</p>
      <p>Lorem ipsum dolor sit amet, consectetur adipisicing elit, sed do eiusmod tempor incididunt ut labore et dolore magna aliqua. Ut enim ad minim veniam, quis nostrud exercitation ullamco laboris nisi ut aliquip ex ea commodo consequat. Duis aute irure dolor in reprehenderit in voluptate velit esse cillum dolore eu fugiat nulla pariatur. Excepteur sint occaecat cupidatat non proident, sunt in culpa qui officia deserunt mollit anim id est laborum.</p>
      <p>Lorem ipsum dolor sit amet, consectetur adipisicing elit, sed do eiusmod tempor incididunt ut labore et dolore magna aliqua. Ut enim ad minim veniam, quis nostrud exercitation ullamco laboris nisi ut aliquip ex ea commodo consequat. Duis aute irure dolor in reprehenderit in voluptate velit esse cillum dolore eu fugiat nulla pariatur. Excepteur sint occaecat cupidatat non proident, sunt in culpa qui officia deserunt mollit anim id est laborum.</p>
      <p class="closing">Yours Sincerely,</p>
    </section>

    <div class="signature" role="img" aria-label="Handwritten signature of the sender"></div>

    <svg class="footer-band" viewBox="0 0 545 11" preserveAspectRatio="none" aria-hidden="true">
      <polygon points="0,0 351,0 355,11 0,11" fill="var(--brand-blue)"/>
      <polygon points="354,0 545,0 545,11 358,11" fill="var(--brand-grey)"/>
    </svg>
  </main>
</body>
</html>
```